Keystone Trench Co Business Card*

Looking for a professional, clean and crisp business card

I am in the underground utilities industry and am just looking for a really impressive business card. I would like our card to be white with our symbol crisp and clear with it protruding. I also have a business partner that will require his name and info on the card once the design is set. I would like to have our website info on the card which is;
http://keystonetrenchco.example/

Contact Information for Business Card

Website, contact name, number and email

```html
<!DOCTYPE html>
<html lang="en">
<head>
<meta charset="utf-8">
<title>Keystone Trench Co Business Card</title>
<link rel="stylesheet" href="https://fonts.googleapis.com/css2?family=Bebas+Neue&family=Oswald:wght@400;500&display=swap">
<style>
  :root {
    --backdrop: #a9b0b2;
    --card: #f7f7f5;
    --ink: #1f1f1f;
    --detail: #4a4a4a;
    --brand-blue: #3b63b5;
    --accent-red: #e0161c;
    --edge: #1f3c8a;
  }
  html, body {
    margin: 0;
    padding: 0;
    width: 1200px;
    height: 824px;
    overflow: hidden;
    background: var(--backdrop);
  }
  .canvas {
    position: relative;
    width: 1200px;
    height: 824px;
    display: flex;
    align-items: center;
    justify-content: center;
  }
  .card {
    position: relative;
    width: 900px;
    height: 514px;
    background: var(--card);
    border-bottom: 3px solid var(--edge);
    box-shadow: 0 10px 24px rgba(0,0,0,0.18);
    display: flex;
    align-items: center;
    box-sizing: border-box;
    padding: 0 60px;
  }
  .brand {
    flex: 1 1 50%;
    display: flex;
    flex-direction: column;
    align-items: center;
    gap: 22px;
  }
  .brand-dot {
    width: 150px;
    height: 150px;
    border-radius: 50%;
    background: var(--brand-blue);
  }
  .brand-name {
    font-family: "Bebas Neue", "Oswald", sans-serif;
    font-size: 58px;
    line-height: 1;
    color: var(--ink);
    letter-spacing: 1px;
    text-align: center;
  }
  .contact {
    flex: 1 1 50%;
    text-align: right;
    font-family: "Oswald", sans-serif;
    color: var(--detail);
    text-transform: uppercase;
    align-self: flex-start;
    padding-top: 70px;
  }
  .person-name {
    font-family: "Bebas Neue", "Oswald", sans-serif;
    font-size: 50px;
    line-height: 1;
    color: var(--brand-blue);
    letter-spacing: 1px;
    margin: 0;
  }
  .person-title {
    font-family: "Bebas Neue", "Oswald", sans-serif;
    font-size: 24px;
    line-height: 1;
    color: var(--accent-red);
    margin: 2px 0 30px;
  }
  .address, .reach {
    font-size: 17px;
    line-height: 1.35;
    letter-spacing: 0.5px;
    margin: 0;
  }
  .reach { margin-top: 18px; }
  .reach .phone { margin-bottom: 18px; display: block; }
</style>
</head>
<body>
  <main class="canvas">
    <section class="card">
      <div class="brand">
        <div class="brand-dot"></div>
        <div class="brand-name">Keystone Trench Co</div>
      </div>
      <div class="contact">
        <h1 class="person-name">Daniel Reyes</h1>
        <div class="person-title">President</div>
        <p class="address">
          Keystone Trench Co LLC<br>
          4120 Birchwood Lane<br>
          Fairbanks, Alaska 99701
        </p>
        <p class="reach">
          <span class="phone">555-014-7720</span>
          info@keystonetrenchco.example<br>
          www.keystonetrenchco.example
        </p>
      </div>
    </section>
  </main>
</body>
</html>
```